Professional & attention grabbing.

A business card design, front and back. I already have a logo I will attach, but I am open to something new as well.
Things to include:
Name:
Title:
Phone:
Email:
Wanting something that is professional but attention grabbing.
Also we do a lot of work using drones on natural gas pipelines (leading the future)if you want to include any of that. I'm open to ideas.
Target Market(s)
Natural gas transmission industry / greenhouse gas mitigation industry
Industry/Entity Type
Business
Colors
Designer to choose colors to be used in the design.
Look and feel
Each slider illustrates characteristics of the customer's brand and the style your logo design should communicate.

```html
<!DOCTYPE html>
<html lang="en">
<head>
<meta charset="UTF-8">
<title>KV Field Inspections – Business Card</title>
<link href="https://fonts.googleapis.com/css2?family=Roboto+Condensed:wght@400;700&display=swap" rel="stylesheet">
<style>
  :root {
    --brand-red: #c8202a;
    --brand-red-dark: #9e151d;
    --charcoal: #3a3b3d;
    --charcoal-deep: #232426;
    --paper: #ffffff;
    --stage: #e9e9ea;
    --text-light: #f2f2f2;
  }
  * { margin: 0; padding: 0; box-sizing: border-box; }
  html, body {
    width: 1200px; height: 950px; overflow: hidden;
    background: var(--stage);
    font-family: "Roboto Condensed", Arial, sans-serif;
  }
  .sheet {
    position: relative; width: 1200px; height: 950px;
    display: flex; align-items: center; justify-content: center; gap: 44px;
  }
  .card {
    position: relative; width: 530px; height: 303px; overflow: hidden;
    box-shadow: 0 6px 18px rgba(0,0,0,0.18);
  }

  /* ---------- Front ---------- */
  .card-front { background: var(--paper); }
  .card-front .wave { position: absolute; inset: 0; }
  .brand {
    position: absolute; display: flex; align-items: center; gap: 10px;
  }
  .brand-mark { width: 22px; height: 22px; background: var(--brand-red); }
  .brand-name {
    font-weight: 700; text-transform: uppercase; letter-spacing: 0.5px;
    line-height: 1;
  }
  .card-front .brand { top: 34px; right: 34px; }
  .card-front .brand-name { font-size: 30px; color: var(--charcoal); }

  .contact {
    position: absolute; left: 34px; bottom: 22px; color: var(--text-light);
  }
  .contact-name {
    color: var(--brand-red); font-size: 19px; line-height: 22px; letter-spacing: 1px;
    text-transform: uppercase; font-weight: 400;
  }
  .contact-title {
    font-size: 15px; line-height: 18px; text-transform: uppercase; letter-spacing: 0.5px;
    margin-bottom: 10px;
  }
  .contact-list { list-style: none; }
  .contact-list li {
    display: flex; align-items: center; gap: 10px;
    font-size: 14px; line-height: 22px;
  }
  .contact-list svg { width: 13px; height: 13px; fill: var(--brand-red); flex: none; }

  /* ---------- Back ---------- */
  .card-back {
    background: linear-gradient(135deg, var(--brand-red) 0%, #d42a33 50%, var(--brand-red-dark) 100%);
  }
  .card-back .brand {
    top: 50%; left: 50%; transform: translate(-50%, -50%);
  }
  .card-back .brand-mark { width: 30px; height: 30px; background: var(--paper); }
  .card-back .brand-name { font-size: 40px; color: var(--paper); white-space: nowrap; }
  .back-url {
    position: absolute; left: 24px; top: 50%;
    transform: translate(-50%, -50%) rotate(-90deg); transform-origin: center;
    color: var(--text-light); font-size: 12px; letter-spacing: 4px; white-space: nowrap;
  }
</style>
</head>
<body>
<main class="sheet">

  <section class="card card-front" aria-label="Card front">
    <svg class="wave" viewBox="0 0 530 303" preserveAspectRatio="none" aria-hidden="true">
      <path d="M0 104 C 120 142, 260 142, 380 110 C 440 94, 490 80, 530 74 L530 303 L0 303 Z" fill="var(--brand-red)"/>
      <path d="M0 112 C 120 150, 260 150, 380 120 C 440 104, 490 90, 530 84 L530 303 L0 303 Z" fill="var(--charcoal)"/>
      <path d="M0 190 C 140 240, 300 240, 530 170 L530 303 L0 303 Z" fill="var(--charcoal-deep)" opacity="0.35"/>
    </svg>

    <div class="brand">
      <span class="brand-mark"></span>
      <span class="brand-name">KV Field Inspections</span>
    </div>

    <div class="contact">
      <p class="contact-name">Alan Marsh</p>
      <p class="contact-title">President</p>
      <ul class="contact-list">
        <li>
          <svg viewBox="0 0 24 24"><path d="M6.6 10.8a15.5 15.5 0 0 0 6.6 6.6l2.2-2.2a1 1 0 0 1 1-.25 11.4 11.4 0 0 0 3.6.57 1 1 0 0 1 1 1V20a1 1 0 0 1-1 1A17 17 0 0 1 3 4a1 1 0 0 1 1-1h3.5a1 1 0 0 1 1 1c0 1.25.2 2.45.57 3.6a1 1 0 0 1-.25 1z"/></svg>
          <span>555 0142 7789</span>
        </li>
        <li>
          <svg viewBox="0 0 24 24"><path d="M2 5h20v14H2z M2 5l10 8 10-8" fill="none" stroke="var(--brand-red)" stroke-width="2.4"/></svg>
          <span>alan@kvfield.com</span>
        </li>
        <li>
          <svg viewBox="0 0 24 24"><circle cx="12" cy="12" r="9" fill="none" stroke="var(--brand-red)" stroke-width="2.4"/><path d="M3 12h18M12 3c3 3 3 15 0 18M12 3c-3 3-3 15 0 18" fill="none" stroke="var(--brand-red)" stroke-width="1.8"/></svg>
          <span>www.kvfield.com</span>
        </li>
      </ul>
    </div>
  </section>

  <section class="card card-back" aria-label="Card back">
    <p class="back-url">www.kvfield.com</p>
    <div class="brand">
      <span class="brand-mark"></span>
      <span class="brand-name">KV Field Inspections</span>
    </div>
  </section>

</main>
</body>
</html>
```